Help me make landing pages for my web application that are mobile friendly

I need to make 2 mobile friendly landing pages for an application. The 2 pages will be related. First I need a home page and then I need a working page. I do not want to change the color scheme or logos. Just layout and design.

```html
<!DOCTYPE html>
<html lang="en">
<head>
<meta charset="utf-8">
<title>ShiftCover – Mobile Screens</title>
<link href="https://fonts.googleapis.com/css2?family=Montserrat:wght@400;500;600;700&display=swap" rel="stylesheet">
<style>
:root{
  --backdrop:#5f5f5f;
  --white:#ffffff;
  --ink:#1f1f24;
  --muted:#444;
  --teal:#2aa6cb;
  --violet:#6a4fa6;
  --violet-soft:#dcd4f0;
  --panel:#dff0f6;
  --line:#cfd6de;
  --green:#4caf2a;
  --red:#c8333a;
  --grad:linear-gradient(90deg,#38a9cc 0%,#5b82c0 55%,#6b5cb0 100%);
  --field:#f1f1f3;
}
*{box-sizing:border-box;margin:0;padding:0}
html,body{width:722px;height:1200px;overflow:hidden;background:var(--backdrop)}
body{font-family:'Montserrat',sans-serif;color:var(--ink)}
.stage{position:relative;width:1304px;height:2166px;transform:scale(0.5537);transform-origin:0 0}
.abs{position:absolute}
.screen{position:absolute;background:var(--white);overflow:hidden}
.status-bar{position:absolute;left:0;right:0;top:0;height:43px;font-weight:700;font-size:17px}
.status-bar .time{position:absolute;left:14px;top:12px}
.status-bar svg{position:absolute;right:14px;top:14px}
.app-header{position:absolute;left:0;right:0;top:43px;height:82px;background:var(--grad);border-radius:0 0 26px 26px}
.menu-btn{position:absolute;left:15px;top:30px}
.avatar{position:absolute;border-radius:50%;background:radial-gradient(circle at 50% 40%,#d9b9a0,#6d5a52)}
.online{position:absolute;width:12px;height:12px;border-radius:50%;background:var(--green);border:2px solid #fff}
.tabs{position:absolute;top:207px;left:19px;font-size:17px;white-space:nowrap;color:#333}
.tabs span{margin-right:20px}
.tabs .active{color:var(--violet);font-weight:600}
.tab-line{position:absolute;top:187px;left:0;right:0;height:2px;background:#e4e4e4}
.tab-marker{position:absolute;top:185px;left:18px;width:145px;height:3px;background:var(--violet)}
.panel{position:absolute;left:15px;top:226px;width:384px;height:1341px;background:var(--panel);border-radius:20px}
.panel-title{position:absolute;left:25px;top:36px;font-size:21px;font-weight:500}
.help{position:absolute;right:26px;top:34px;font-size:21px;font-weight:500}
.card{position:absolute;left:17px;width:350px;height:188px;background:#fff;border:1px solid #c9dde6;border-radius:8px}
.card .lead{position:absolute;left:22px;top:20px;font-size:18px;font-weight:500}
.card .avatar{left:22px;top:61px;width:58px;height:58px}
.card .name{position:absolute;left:93px;top:61px;font-size:17px;font-weight:500;color:var(--teal)}
.card .role{position:absolute;left:94px;top:83px;font-size:15px;color:#333}
.card .edit{position:absolute;right:22px;top:61px}
.card dl{position:absolute;left:94px;top:108px;font-size:12.5px;line-height:20.5px;display:grid;grid-template-columns:90px auto}
.card dt{font-weight:500}
.card dd{color:#444}
.st{text-decoration:underline}
.st.complete{color:var(--violet)}
.st.active{color:var(--green)}
.st.canceled{color:var(--red)}
.home-bar{position:absolute;height:6px;border-radius:3px;background:var(--grad)}
/* detail screen */
.detail{position:absolute;left:15px;top:157px;width:385px;height:1843px;border:1.5px solid var(--teal);border-radius:18px}
.detail .t{position:absolute;font-size:15.5px;line-height:23px}
.detail h2{position:absolute;left:15px;top:28px;font-size:20px;font-weight:500}
.box{position:absolute;left:15px;width:354px;border:1px solid #9aa0a8;border-radius:6px}
.input{position:absolute;border:1px solid #8d949c;border-radius:7px;font-size:15.5px;padding:9px 12px}
.placeholder{color:#aaa;font-size:13.5px;line-height:21px}
.icon-btn{position:absolute;width:36px;height:36px;border-radius:8px;background:var(--violet-soft);display:flex;align-items:center;justify-content:center}
.notice{position:absolute;left:12px;top:150px;width:329px;height:36px;border-radius:7px;background:var(--teal);color:#fff;font-size:16px;font-weight:500;display:flex;align-items:center;justify-content:center}
.chip{position:absolute;top:65px;height:38px;border-radius:7px;background:#eceef0;font-size:16px;display:flex;align-items:center;gap:6px;padding:0 14px}
.date-row{position:absolute;left:12px;width:329px;height:38px;border-radius:7px;background:var(--field);border:1px solid #e0e0e0;font-size:16px}
.date-row .cb{position:absolute;left:12px;top:10px;width:15px;height:15px;border:2px solid #333;border-radius:2px}
.date-row .val{position:absolute;left:44px;top:8px}
.date-row .ic{position:absolute;right:12px;top:10px}
.date-row .sep,.time-field .sep{position:absolute;right:39px;top:6px;width:1px;height:24px;background:#333}
.time-field{position:absolute;left:11px;width:330px;height:37px;border:1px solid #8d949c;border-radius:7px;font-size:16px}
.time-field .val{position:absolute;left:13px;top:7px}
.time-field .ic{position:absolute;right:10px;top:9px}
.rule{position:absolute;left:12px;width:329px;height:1px;background:#ccc}
.action{position:absolute;top:746px;height:36px;width:104px;border-radius:7px;background:var(--violet);color:#fff;font-size:16px;display:flex;align-items:center;justify-content:center;gap:6px}
/* drawer */
.drawer{position:absolute;left:1021px;top:56px;width:234px;height:457px;background:var(--violet);color:#fff}
.brand{position:absolute;left:20px;top:30px;display:flex;align-items:center;gap:10px;font-size:28px;font-weight:500}
.brand .dot{width:22px;height:22px;border-radius:50%;background:#fff}
.nav-home{position:absolute;left:13px;top:104px;width:210px;height:36px;border-radius:4px;background:#28acd0;font-size:15px;font-weight:600;display:flex;align-items:center;padding-left:16px;gap:10px}
.nav-item{position:absolute;left:30px;font-size:15px;display:flex;align-items:center;gap:13px}
.user{position:absolute;left:0;right:0;top:344px;text-align:center}
.user .nm{font-size:17px;font-weight:600}
.user .em{font-size:13px;margin-top:2px}
.drawer .divider{position:absolute;left:15px;right:13px;top:397px;height:1px;background:#b9a9dc}
.logout{position:absolute;left:74px;top:410px;font-size:15px;font-weight:600;display:flex;align-items:center;gap:9px}
</style>
</head>
<body>
<div class="stage">

  <!-- Home screen -->
  <section class="screen" style="left:49px;top:55px;width:414px;height:1607px">
    <div class="status-bar"><span class="time">9:45</span>
      <svg width="78" height="14" viewBox="0 0 78 14"><rect x="0" y="9" width="3" height="4" fill="#111"/><rect x="5" y="6" width="3" height="7" fill="#111"/><rect x="10" y="3" width="3" height="10" fill="#111"/><rect x="15" y="0" width="3" height="13" fill="#111"/><path d="M26 5 a11 11 0 0 1 16 0 M29 8 a6 6 0 0 1 10 0" stroke="#111" stroke-width="2.2" fill="none"/><circle cx="34" cy="11.5" r="1.8" fill="#111"/><rect x="50" y="1" width="24" height="12" rx="3" fill="#111"/><rect x="75" y="5" width="2" height="4" fill="#111"/></svg>
    </div>
    <header class="app-header">
      <svg class="menu-btn" width="27" height="20" viewBox="0 0 27 20"><path d="M0 2h27M0 10h27M0 18h27" stroke="#fff" stroke-width="2.6"/></svg>
      <div class="avatar" role="img" aria-label="User profile photo" style="left:344px;top:17px;width:48px;height:48px"></div>
      <span class="online" style="left:380px;top:14px"></span>
    </header>
    <nav class="tabs"><span class="active">My Assignments</span><span>Available Openings</span><span>My Assignments</span></nav>
    <div class="tab-line"></div><div class="tab-marker"></div>

    <div class="panel">
      <h1 class="panel-title">My Assignments</h1><span class="help">?</span>

      <article class="card" style="top:79px"><span class="lead">Subbing For:</span>
        <div class="avatar" role="img" aria-label="Portrait photo"></div>
        <span class="name">Nora Whitfield</span><span class="role">Teacher</span>
        <svg class="edit" width="18" height="18" viewBox="0 0 18 18"><path d="M14 10v6H2V4h6" stroke="#222" stroke-width="2" fill="none"/><path d="M7 11l1-3 7-7 2 2-7 7z" fill="#222"/></svg>
        <dl><dt>Location:</dt><dd>MRES</dd><dt>Status:</dt><dd><span class="st complete">Complete</span></dd><dt>Time Slots:</dt><dd>09/02 - 09/02 (1h 0m)</dd></dl>
      </article>
      <article class="card" style="top:286px"><span class="lead">Subbing For:</span>
        <div class="avatar" role="img" aria-label="Portrait photo"></div>
        <span class="name">Extra duty</span><span class="role">Teacher</span>
        <svg class="edit" width="18" height="18" viewBox="0 0 18 18"><path d="M14 10v6H2V4h6" stroke="#222" stroke-width="2" fill="none"/><path d="M7 11l1-3 7-7 2 2-7 7z" fill="#222"/></svg>
        <dl><dt>Location:</dt><dd>MRES</dd><dt>Status:</dt><dd><span class="st complete">Complete</span></dd><dt>Time Slots:</dt><dd>09/02 - 09/02 (1h 0m)</dd></dl>
      </article>
      <article class="card" style="top:494px"><span class="lead">Subbing For:</span>
        <div class="avatar" role="img" aria-label="Portrait photo"></div>
        <span class="name">Owen Calder</span><span class="role">Teacher</span>
        <svg class="edit" width="18" height="18" viewBox="0 0 18 18"><path d="M14 10v6H2V4h6" stroke="#222" stroke-width="2" fill="none"/><path d="M7 11l1-3 7-7 2 2-7 7z" fill="#222"/></svg>
        <dl><dt>Location:</dt><dd>MRES</dd><dt>Status:</dt><dd><span class="st complete">Complete</span></dd><dt>Time Slots:</dt><dd>09/02 - 09/02 (1h 0m)</dd></dl>
      </article>
      <article class="card" style="top:701px"><span class="lead">Subbing For:</span>
        <div class="avatar" role="img" aria-label="Portrait photo"></div>
        <span class="name">Reid Ashford</span><span class="role">Teacher</span>
        <svg class="edit" width="18" height="18" viewBox="0 0 18 18"><path d="M14 10v6H2V4h6" stroke="#222" stroke-width="2" fill="none"/><path d="M7 11l1-3 7-7 2 2-7 7z" fill="#222"/></svg>
        <dl><dt>Location:</dt><dd>MRES</dd><dt>Status:</dt><dd><span class="st active">Active</span></dd><dt>Time Slots:</dt><dd>09/02 - 09/02 (1h 0m)</dd></dl>
      </article>
      <article class="card" style="top:909px"><span class="lead">Subbing For:</span>
        <div class="avatar" role="img" aria-label="Portrait photo"></div>
        <span class="name">Lena Rosewood</span><span class="role">Teacher</span>
        <svg class="edit" width="18" height="18" viewBox="0 0 18 18"><path d="M14 10v6H2V4h6" stroke="#222" stroke-width="2" fill="none"/><path d="M7 11l1-3 7-7 2 2-7 7z" fill="#222"/></svg>
        <dl><dt>Location:</dt><dd>MRES</dd><dt>Status:</dt><dd><span class="st canceled">Canceled</span></dd><dt>Time Slots:</dt><dd>09/02 - 09/02 (1h 0m)</dd></dl>
      </article>
      <article class="card" style="top:1116px"><span class="lead">Subbing For:</span>
        <div class="avatar" role="img" aria-label="Portrait photo"></div>
        <span class="name">Miles Harrow</span><span class="role">Teacher</span>
        <svg class="edit" width="18" height="18" viewBox="0 0 18 18"><path d="M14 10v6H2V4h6" stroke="#222" stroke-width="2" fill="none"/><path d="M7 11l1-3 7-7 2 2-7 7z" fill="#222"/></svg>
        <dl><dt>Location:</dt><dd>MRES</dd><dt>Status:</dt><dd><span class="st active">Active</span></dd><dt>Time Slots:</dt><dd>09/02 - 09/02 (1h 0m)</dd></dl>
      </article>
    </div>
    <div class="home-bar" style="left:50px;top:1599px;width:314px"></div>
  </section>

  <!-- Working screen -->
  <section class="screen" style="left:536px;top:55px;width:414px;height:2057px">
    <div class="status-bar"><span class="time">9:45</span>
      <svg width="78" height="14" viewBox="0 0 78 14"><rect x="0" y="9" width="3" height="4" fill="#111"/><rect x="5" y="6" width="3" height="7" fill="#111"/><rect x="10" y="3" width="3" height="10" fill="#111"/><rect x="15" y="0" width="3" height="13" fill="#111"/><path d="M26 5 a11 11 0 0 1 16 0 M29 8 a6 6 0 0 1 10 0" stroke="#111" stroke-width="2.2" fill="none"/><circle cx="34" cy="11.5" r="1.8" fill="#111"/><rect x="50" y="1" width="24" height="12" rx="3" fill="#111"/><rect x="75" y="5" width="2" height="4" fill="#111"/></svg>
    </div>
    <header class="app-header">
      <svg class="menu-btn" width="27" height="20" viewBox="0 0 27 20"><path d="M0 2h27M0 10h27M0 18h27" stroke="#fff" stroke-width="2.6"/></svg>
      <div class="avatar" role="img" aria-label="User profile photo" style="left:344px;top:17px;width:48px;height:48px"></div>
      <span class="online" style="left:380px;top:14px"></span>
    </header>

    <div class="detail">
      <h2>Opening Information</h2>
      <span class="t" style="left:15px;top:82px">Summary :</span><span class="t" style="left:167px;top:82px">Testing-test</span>
      <span class="t" style="left:15px;top:126px">Location :</span><span class="t" style="left:167px;top:126px">Maple Ridge Elementary<br>School</span>
      <span class="t" style="left:15px;top:193px">Type :</span><span class="t" style="left:167px;top:193px">Vacancy</span>
      <span class="t" style="left:15px;top:235px">Regular Staff :</span><span class="t" style="left:167px;top:235px">Owen Calder</span>
      <span class="t" style="left:15px;top:281px">Assignment<br>Category :</span><span class="t" style="left:167px;top:282px">Teacher</span>
      <span class="t" style="left:15px;top:347px">Department :</span><span class="t" style="left:167px;top:345px">-----</span>
      <span class="t" style="left:15px;top:391px">Description :</span>
      <div class="box" style="top:427px;height:90px;padding:9px 12px;font-size:15.5px;line-height:21px;color:#444">asdf<br>sffsd</div>

      <div class="box" style="top:555px;height:212px">
        <span class="t" style="left:12px;top:18px">Comments :</span>
        <div class="input" style="left:11px;top:54px;width:282px;height:78px"><span class="placeholder">Write a comment or upload a File...</span></div>
        <div class="icon-btn" style="left:305px;top:54px"><svg width="18" height="18" viewBox="0 0 18 18"><path d="M1 8L17 1 12 17 9 10z" fill="var(--violet)"/></svg></div>
        <div class="icon-btn" style="left:305px;top:96px"><svg width="18" height="18" viewBox="0 0 18 18"><path d="M12 5l-6 6a2 2 0 0 0 3 3l7-7a4 4 0 0 0-6-6L3 8a5 5 0 0 0 7 7l5-5" stroke="var(--violet)" stroke-width="1.8" fill="none"/></svg></div>
        <div class="notice">No comments or files uploaded</div>
      </div>

      <div class="box" style="top:805px;height:155px">
        <span class="t" style="left:12px;top:20px">Additional Details :</span>
        <span class="t" style="left:12px;top:59px">Parking Spot</span>
        <div class="input" style="left:11px;top:91px;width:330px;height:37px"></div>
      </div>

      <div class="box" style="top:998px;height:811px">
        <span class="t" style="left:12px;top:21px">Time Slots :</span>
        <div class="chip" style="left:12px;width:120px"><svg width="16" height="16" viewBox="0 0 16 16"><rect x="1" y="3" width="14" height="12" rx="1" stroke="#222" stroke-width="1.8" fill="none"/><path d="M4 1v4M12 1v4M5 9l2 2 4-4" stroke="#222" stroke-width="1.8" fill="none"/></svg>Accept</div>
        <div class="chip" style="left:142px;width:135px"><svg width="16" height="16" viewBox="0 0 16 16"><rect x="1" y="3" width="14" height="12" rx="1" stroke="#222" stroke-width="1.8" fill="none"/><path d="M4 1v4M12 1v4M1 7h14" stroke="#222" stroke-width="1.8" fill="none"/></svg>Withdraw</div>

        <div class="date-row" style="top:123px"><span class="cb"></span><span class="val">3/19/2026</span><span class="sep"></span><svg class="ic" width="16" height="16" viewBox="0 0 16 16"><rect x="2" y="1" width="12" height="14" rx="1" stroke="#222" stroke-width="1.8" fill="none"/><path d="M4 5h8M5 9h2M9 9h2M5 12h2M9 12h2" stroke="#222" stroke-width="1.8"/></svg></div>
        <div class="rule" style="top:185px"></div>
        <span class="t" style="left:11px;top:205px">From :</span>
        <div class="time-field" style="top:235px"><span class="val">9:30 AM</span><span class="sep"></span><svg class="ic" width="17" height="17" viewBox="0 0 17 17"><circle cx="8.5" cy="8.5" r="8" fill="#111"/><path d="M8.5 4v5l3 2" stroke="#fff" stroke-width="1.8" fill="none"/></svg></div>
        <span class="t" style="left:11px;top:287px">To :</span>
        <div class="time-field" style="top:317px"><span class="val">12:30 AM</span><span class="sep"></span><svg class="ic" width="17" height="17" viewBox="0 0 17 17"><circle cx="8.5" cy="8.5" r="8" fill="#111"/><path d="M8.5 4v5l3 2" stroke="#fff" stroke-width="1.8" fill="none"/></svg></div>
        <span class="t" style="left:11px;top:370px">Current<br>Assignment :</span><span class="t" style="left:152px;top:370px">No Assignment</span>
        <span class="t" style="left:11px;top:437px">Status :</span><span class="t" style="left:152px;top:438px">Active</span>

        <div class="date-row" style="top:484px"><span class="cb"></span><span class="val">3/19/2026</span><span class="sep"></span><svg class="ic" width="16" height="16" viewBox="0 0 16 16"><rect x="2" y="1" width="12" height="14" rx="1" stroke="#222" stroke-width="1.8" fill="none"/><path d="M4 5h8M5 9h2M9 9h2M5 12h2M9 12h2" stroke="#222" stroke-width="1.8"/></svg></div>
        <div class="rule" style="top:546px"></div>
        <span class="t" style="left:11px;top:566px">From :</span>
        <div class="time-field" style="top:596px"><span class="val">9:30 AM</span><span class="sep"></span><svg class="ic" width="17" height="17" viewBox="0 0 17 17"><circle cx="8.5" cy="8.5" r="8" fill="#111"/><path d="M8.5 4v5l3 2" stroke="#fff" stroke-width="1.8" fill="none"/></svg></div>
        <span class="t" style="left:11px;top:648px">To :</span>
        <div class="time-field" style="top:678px"><span class="val">12:30 AM</span><span class="sep"></span><svg class="ic" width="17" height="17" viewBox="0 0 17 17"><circle cx="8.5" cy="8.5" r="8" fill="#111"/><path d="M8.5 4v5l3 2" stroke="#fff" stroke-width="1.8" fill="none"/></svg></div>

        <div class="action" style="left:64px"><svg width="14" height="14" viewBox="0 0 14 14"><rect width="14" height="14" rx="2" fill="#fff"/><path d="M3 7l3 3 5-6" stroke="var(--violet)" stroke-width="2" fill="none"/></svg>Save</div>
        <div class="action" style="left:184px"><svg width="14" height="14" viewBox="0 0 14 14"><rect width="14" height="14" rx="2" fill="#fff"/><path d="M4 4l6 6M10 4l-6 6" stroke="var(--violet)" stroke-width="2"/></svg>Close</div>
      </div>
    </div>
    <div class="home-bar" style="left:50px;top:2049px;width:314px"></div>
  </section>

  <!-- Navigation drawer -->
  <aside class="drawer">
    <div class="brand"><span class="dot"></span>ShiftCover</div>
    <div class="nav-home"><svg width="18" height="16" viewBox="0 0 18 16"><path d="M9 0L0 8h3v8h4v-5h4v5h4V8h3z" fill="#fff"/></svg>Home</div>
    <div class="nav-item" style="top:159px"><svg width="12" height="15" viewBox="0 0 12 15"><path d="M0 0h8l4 4v11H0z" fill="#fff"/></svg>Available Openings</div>
    <div class="nav-item" style="top:196px"><svg width="12" height="15" viewBox="0 0 12 15"><path d="M0 0h8l4 4v11H0z" fill="#fff"/></svg>Assignments</div>
    <div class="nav-item" style="top:232px"><svg width="15" height="15" viewBox="0 0 15 15"><path d="M3 8V3a1 1 0 0 1 2 0v4V1a1 1 0 0 1 2 0v6V2a1 1 0 0 1 2 0v5V4a1 1 0 0 1 2 0v6a5 5 0 0 1-9 2L0 9a1 1 0 0 1 2-1z" fill="#fff"/></svg>Support</div>
    <svg class="abs" style="left:208px;top:236px" width="9" height="13" viewBox="0 0 9 13"><path d="M2 1l5 5.5L2 12" stroke="#fff" stroke-width="2" fill="none"/></svg>
    <div class="user"><div class="nm">Greta</div><div class="em">g.sub2@mailbox.test</div></div>
    <div class="divider"></div>
    <div class="logout"><svg width="16" height="14" viewBox="0 0 16 14"><path d="M6 1H1v12h5M5 7h10M11 3l4 4-4 4" stroke="#fff" stroke-width="2" fill="none"/></svg>Log Out</div>
  </aside>
</div>
</body>
</html>
```